MRT Property - Business Cards

Looking for a business card & general letterhead, signage etc design for our new logo.

Colours:
000a20
0056a2
00b5ef
0088ce
68cef2

Fonts:
Poppins
Karla

Please keep look and feel of new brand - example in the zip package I sent.

```html
<!DOCTYPE html>
<html lang="en">
<head>
<meta charset="utf-8">
<title>MRT Property – Business Cards</title>
<link rel="stylesheet" href="https://fonts.googleapis.com/css2?family=Poppins:wght@400;500;600;700&display=swap">
<style>
  :root {
    --stage: #d9d4cc;
    --card-white: #ffffff;
    --navy: #0056a2;
    --sky: #29a8e0;
    --back-blue: #1287cc;
    --back-mark: #0a6db0;
    --ink: #3a3a3a;
    --muted: #555a60;
    --rule: #2d6fb0;
  }
  * { box-sizing: border-box; margin: 0; padding: 0; }
  html, body { width: 900px; height: 1200px; overflow: hidden; }
  body {
    position: relative;
    background: var(--stage);
    font-family: "Poppins", sans-serif;
  }
  .card {
    position: absolute;
    left: 80px;
    width: 742px;
    height: 440px;
    border-radius: 30px;
    overflow: hidden;
  }
  .card--front { top: 132px; background: var(--card-white); }
  .card--back { top: 638px; background: var(--back-blue); }

  .brand {
    position: absolute;
    display: flex;
    align-items: center;
    gap: 14px;
    font-weight: 600;
    white-space: nowrap;
  }
  .brand__dot { border-radius: 50%; flex: none; }
  .card--front .brand { left: 37px; top: 62px; font-size: 44px; color: var(--navy); }
  .card--front .brand__dot { width: 30px; height: 30px; background: var(--navy); }

  .card--back .brand {
    left: 0; right: 0; top: 0; bottom: 0;
    justify-content: center;
    font-size: 84px;
    color: var(--back-mark);
  }
  .card--back .brand__dot { width: 54px; height: 54px; background: var(--back-mark); }

  .holder { position: absolute; left: 37px; top: 276px; }
  .holder__name { font-size: 27px; font-weight: 600; color: var(--sky); line-height: 1.1; }
  .holder__role { font-size: 16px; color: var(--muted); margin-top: 2px; }

  .rule {
    position: absolute;
    left: 37px; top: 333px;
    width: 672px; height: 1.5px;
    background: var(--rule);
  }

  .contacts {
    position: absolute;
    left: 37px; top: 345px;
    list-style: none;
  }
  .contacts li {
    display: flex; align-items: center; gap: 12px;
    font-size: 16px; color: var(--ink);
    height: 22px;
  }
  .contacts svg { width: 14px; height: 14px; fill: var(--sky); flex: none; }

  .address {
    position: absolute;
    left: 475px; top: 366px;
    font-size: 16px; line-height: 20px;
    color: var(--ink);
    font-style: normal;
  }
</style>
</head>
<body>

<section class="card card--front" aria-label="Business card front">
  <div class="brand"><span class="brand__dot"></span>MRT Property</div>

  <div class="holder">
    <p class="holder__name">Dana Whitcombe</p>
    <p class="holder__role">Owner</p>
  </div>

  <div class="rule"></div>

  <ul class="contacts">
    <li>
      <svg viewBox="0 0 16 16" aria-hidden="true"><path d="M3 1h3l1.5 4-2 1.3a9 9 0 0 0 4.2 4.2L11 8.5l4 1.5v3a2 2 0 0 1-2 2A12 12 0 0 1 1 3a2 2 0 0 1 2-2z"/></svg>
      555-014-2290
    </li>
    <li>
      <svg viewBox="0 0 16 16" aria-hidden="true"><path d="M1 3h14v1.2L8 9 1 4.2z"/><path d="M1 5.8 8 10.6l7-4.8V13H1z"/></svg>
      info@mrtproperty.com.au
    </li>
    <li>
      <svg viewBox="0 0 16 16" aria-hidden="true"><circle cx="8" cy="8" r="7"/><path d="M1.5 8h13M8 1c2.5 2 2.5 12 0 14M8 1c-2.5 2-2.5 12 0 14" stroke="#fff" stroke-width="1" fill="none"/></svg>
      www.mrtproperty.com.au
    </li>
  </ul>

  <address class="address">
    48 Harbor Lane, Suite 210<br>
    Ashford, PA 19000
  </address>
</section>

<section class="card card--back" aria-label="Business card back">
  <div class="brand"><span class="brand__dot"></span>MRT Property</div>
</section>

</body>
</html>
```